Business Card Design - Service Company

Use of the card mainly in living rooms and relations b2b We wish a card with a modern design, blue tones in the background would be a plus The card must be front / back (one side with the logo / the other with the information of contact )

Font styles to use
Serif

Requirements
Must have
• Using the map on the back of the business card Editable format! Photoshop CS2 / Illustrator CS2
Nice to have
• Mivrel Data IT Plein Ouest Commercial Center, 20417 Valmoriccio 0491847352 Siret 41873306200018 APE 9511Z https://www.fb.com/boutiquetech.mivreldata www.mivrel-data.com

```html
<!DOCTYPE html>
<html lang="en">
<head>
<meta charset="utf-8">
<title>Mivrel Data IT — Business Card</title>
<link href="https://fonts.googleapis.com/css2?family=Open+Sans:wght@400;600;700&display=swap" rel="stylesheet">
<style>
  :root {
    --page-bg: #e9e6e1;
    --blue: #2f8ad6;
    --blue-light: #4aa3e8;
    --blue-dark: #1f6fb6;
    --ink: #3a3f45;
    --ink-soft: #6b7178;
    --white: #ffffff;
    --card-shadow: rgba(0, 0, 0, 0.28);
  }
  * { margin: 0; padding: 0; box-sizing: border-box; }
  html, body {
    width: 900px; height: 1200px; overflow: hidden;
    background: var(--page-bg);
    font-family: "Open Sans", Arial, sans-serif;
  }
  .canvas { position: relative; width: 900px; height: 1200px; }

  .card {
    position: absolute;
    width: 600px; height: 460px;
    border-radius: 70px 14px 70px 14px;
    box-shadow: 0 10px 24px var(--card-shadow);
    overflow: hidden;
  }

  /* Front */
  .card-front {
    left: 165px; top: 135px;
    background: linear-gradient(160deg, var(--blue-light) 0%, var(--blue) 55%, var(--blue-dark) 100%);
    color: var(--white);
  }
  .front-brand {
    position: absolute; left: 0; right: 0; top: 175px;
    display: flex; align-items: center; justify-content: center; gap: 16px;
  }
  .brand-mark { width: 26px; height: 26px; background: var(--white); }
  .brand-name { font-weight: 700; font-size: 52px; letter-spacing: -0.5px; line-height: 1; }
  .front-brand .brand-name { color: var(--white); }
  .front-web {
    position: absolute; left: 0; right: 0; top: 350px;
    text-align: center; font-size: 17px; font-weight: 400; letter-spacing: 0.3px;
  }

  /* Back */
  .card-back {
    left: 135px; top: 640px;
    background: var(--white);
    color: var(--ink);
  }
  .back-brand {
    position: absolute; left: 40px; top: 150px;
    display: flex; align-items: center; gap: 10px;
  }
  .back-brand .brand-mark { width: 16px; height: 16px; background: var(--blue); }
  .back-brand .brand-name { font-size: 30px; color: var(--blue); }
  .divider {
    position: absolute; left: 282px; top: 100px; width: 3px; height: 180px;
    background: var(--blue);
  }
  .person { position: absolute; left: 305px; top: 105px; }
  .person-name {
    font-size: 24px; font-weight: 600; color: var(--blue); letter-spacing: 0.5px;
    text-transform: uppercase;
  }
  .person-role { font-size: 15px; color: var(--ink-soft); margin-top: 2px; }
  .contacts { list-style: none; margin-top: 24px; }
  .contacts li {
    display: flex; align-items: center; gap: 10px;
    font-size: 15px; color: var(--ink); line-height: 26px;
  }
  .contacts svg { width: 15px; height: 15px; flex: none; }

  .address-band {
    position: absolute; left: 0; right: 0; top: 340px; height: 30px;
    background: var(--blue); color: var(--white);
    font-size: 15px; font-weight: 700; text-align: center; line-height: 30px;
  }
  .address-lines {
    position: absolute; left: 0; right: 0; top: 378px;
    text-align: center; font-size: 15px; font-weight: 600; line-height: 24px; color: var(--ink);
  }
</style>
</head>
<body>
<main class="canvas">

  <section class="card card-front" aria-label="Card front">
    <div class="front-brand">
      <span class="brand-mark"></span>
      <span class="brand-name">Mivrel Data IT</span>
    </div>
    <p class="front-web">www.mivrel-data.com</p>
  </section>

  <section class="card card-back" aria-label="Card back">
    <div class="back-brand">
      <span class="brand-mark"></span>
      <span class="brand-name">Mivrel Data IT</span>
    </div>
    <div class="divider"></div>
    <div class="person">
      <p class="person-name">Alric Venmore</p>
      <p class="person-role">Founder &amp; CEO</p>
      <ul class="contacts">
        <li>
          <svg viewBox="0 0 16 16"><path fill="#2f8ad6" d="M4 1l2.5 3-1.5 2c1 2 3 4 5 5l2-1.5 3 2.5-1.5 2C8 15 1 8 2 2.5z"/></svg>
          0491 847 350
        </li>
        <li>
          <svg viewBox="0 0 16 16"><rect x="1" y="3" width="14" height="10" rx="1.5" fill="#2f8ad6"/><path d="M1.5 4l6.5 5 6.5-5" stroke="#fff" stroke-width="1.3" fill="none"/></svg>
          info@mivrel-data.com
        </li>
        <li>
          <svg viewBox="0 0 16 16"><circle cx="8" cy="8" r="7" fill="#2f8ad6"/><path d="M1 8h14M8 1c-3 3.5-3 10.5 0 14M8 1c3 3.5 3 10.5 0 14" stroke="#fff" stroke-width="1" fill="none"/></svg>
          www.mivrel-data.com
        </li>
        <li>
          <svg viewBox="0 0 16 16"><circle cx="8" cy="8" r="7" fill="#2f8ad6"/></svg>
          /boutiquetech.mivreldata
        </li>
      </ul>
    </div>
    <div class="address-band">Mivrel Data IT Plein Ouest Commercial Center</div>
    <div class="address-lines">
      <p>20417 Valmoriccio 0491847352</p>
      <p>Siret 41873306200018 APE 9511Z</p>
    </div>
  </section>

</main>
</body>
</html>
```